Fun Employee News and Engagement Portal - Tidy Hearth Company

We are looking for a clean, but fun WordPress template for an internal employee engagement website. The site will be a place we share news, fun stories and pictures. We'll provide space for our employees to post comments, etc.
We are a deep dish pizza restaurant with a rich history. I'd love to see your take on a look and feel for us! The site will be called Bim-Zee. I've posted some images and colors along with this brief description.
Focus on making the template whimsical and fun! (Extra point for focusing on the "Lettering in lights" ).
I will continue to post additional pieces of art and content examples.
Reason: Our team is continuing to review designs. We've decided to extend the timing a few more days. Good luck! Make it playful!
Reason: We need more time with our team to review these designs. We are going to extend one more time!
Reason: Still trying to get enough time to review with the Bim-Zee team!
Reason: We are continuing to evaluate designs. Thank you!
Industry/Entity Type
American Restaurant
Number of Pages Required
1 page
Look and feel
Each slider illustrates characteristics of the customer's brand and the style your logo design should communicate.

```html
<!DOCTYPE html>
<html lang="en">
<head>
<meta charset="utf-8">
<title>Bim-Zee — Tidy Hearth Company</title>
<link rel="stylesheet" href="https://fonts.googleapis.com/css2?family=Arvo:wght@400;700&family=Open+Sans:wght@400;600;700&display=swap">
<style>
:root{
  --red:#e8262d;
  --red-dark:#c91c22;
  --ink:#1f1f1f;
  --text:#555;
  --muted:#8a8a8a;
  --line:#dcdcdc;
  --paper:#fff;
  --soft:#f5f5f5;
}
*{box-sizing:border-box;margin:0;padding:0}
html,body{width:1200px;height:3291px;overflow:hidden;background:var(--paper)}
body{font-family:"Open Sans",Arial,sans-serif;color:var(--text);position:relative}
.abs{position:absolute}
.slab{font-family:"Arvo",Georgia,serif}
h2.section-title{font-family:"Arvo",Georgia,serif;font-weight:700;font-size:24px;color:var(--ink);letter-spacing:.5px;text-transform:uppercase}
.photo{border-radius:2px}

/* header */
.brand{left:99px;top:26px;font-family:"Arvo",Georgia,serif;font-weight:700;font-size:36px;color:#333;display:flex;align-items:center;gap:10px}
.brand .dot{width:14px;height:14px;border-radius:50%;background:var(--red)}
.topbar{right:99px;top:12px;display:flex;gap:18px;align-items:center;font-size:17px;color:#333}
.phone{display:flex;align-items:center;gap:8px}
.login{border:2px solid var(--red);color:var(--red);border-radius:20px;padding:4px 16px;font-size:14px;font-weight:700}
.nav{right:99px;top:56px;display:flex;gap:38px;font-family:"Arvo",Georgia,serif;font-weight:700;font-size:16px;color:#222;align-items:center}
.nav .on{color:var(--red)}

/* hero */
.hero{left:0;top:92px;width:1200px;height:439px;background:var(--red)}
.hero-title{left:99px;top:108px;font-family:"Arvo",Georgia,serif;font-weight:700;font-size:56px;color:#fff}
.hero-rule{left:99px;top:186px;width:453px;height:2px;background:#fff}
.hero-text{left:99px;top:206px;width:520px;font-size:19px;line-height:28px;color:#fff}
.hero-btn{left:99px;top:281px;width:191px;height:40px;border:2px solid #fff;border-radius:22px;color:#fff;font-size:14px;font-weight:700;display:flex;align-items:center;justify-content:center}
.hero-pizza{left:670px;top:-12px;width:460px;height:460px;border-radius:50%;background:radial-gradient(circle,#d7432b 0%,#b82a1a 60%,#5b3a24 100%)}
.slide-arrow{top:185px;width:28px;height:70px;background:rgba(0,0,0,.18);display:flex;align-items:center;justify-content:center}

/* news */
.news-card{top:647px;width:318px}
.news-card .photo{height:204px;position:relative;border:3px solid #e8e8e8}
.tag{position:absolute;left:0;top:0;background:#333;color:#fff;font-size:12px;font-weight:700;padding:5px 14px}
.news-card h3{margin-top:20px;font-size:17px;line-height:24px;font-weight:600;color:#222}
.meta{font-size:12px;color:var(--muted);display:flex;gap:8px;align-items:center}
.meta .r{color:var(--red)}
.news-card .meta{margin-top:8px}
.divider{left:99px;top:1003px;width:1002px;height:1px;background:var(--line)}
.pager-pair{left:548px;top:980px;display:flex;gap:8px}
.circle-btn{width:46px;height:46px;border-radius:50%;border:2px solid #ccc;background:#fff;display:flex;align-items:center;justify-content:center}

/* stories */
.story{left:99px;width:603px;height:582px;border:2px solid #e2e2e2;box-shadow:0 2px 6px rgba(0,0,0,.08);background:#fff}
.story .photo{position:absolute;left:10px;top:10px;width:579px;height:311px}
.story h3{position:absolute;left:18px;top:342px;font-size:19px;font-weight:700;color:#222}
.story .meta{position:absolute;left:18px;top:384px}
.story p{position:absolute;left:18px;top:414px;width:560px;font-size:13px;line-height:26px;color:#666}
.story .more{position:absolute;left:18px;top:504px;font-size:13px;font-weight:700;color:var(--red)}
.share-bar{position:absolute;left:0;bottom:0;width:100%;height:42px;border-top:1px solid #e6e6e6;background:#fafafa;display:flex;align-items:center;padding:0 14px;gap:8px;font-size:12px}
.pill{border:1px solid #cfd6e0;border-radius:3px;padding:2px 8px;background:#eef2f7;color:#345;font-weight:700}
.count{border:1px solid #ddd;padding:2px 6px;background:#fff;color:#555}
.share-bar .end{margin-left:auto;color:#777}
.pagination{left:99px;top:2347px;display:flex;gap:6px;font-size:12px}
.pagination span{border:1px solid #ddd;padding:3px 9px;color:#444;background:#fff}
.pagination .on{background:var(--red);color:#fff;border-color:var(--red)}

/* sidebar */
.side{left:742px;width:359px}
.box{border:2px solid #e2e2e2;background:#fff;box-shadow:0 2px 6px rgba(0,0,0,.06)}
.email-input{border:1px solid #ccc;height:46px;font-size:11px;color:#999;display:flex;align-items:center;padding-left:16px;letter-spacing:.3px}
.red-btn{background:var(--red);color:#fff;font-weight:700;border-radius:24px;display:flex;align-items:center;justify-content:center}
.small{font-size:12px;line-height:20px;color:#777}
.side-rule{height:1px;background:var(--line)}
.blog-item{display:flex;gap:20px}
.blog-item .photo{width:110px;height:83px;border:3px solid #e8e8e8;flex:none}
.blog-item h4{font-size:15px;line-height:20px;font-weight:600;color:var(--red-dark)}

/* gallery */
.gallery{left:99px;top:2519px;display:flex;gap:4px}
.gallery .photo{width:248px;height:197px}
.rule{left:99px;width:1002px;height:1px;background:var(--line)}
.partner{top:2808px;height:78px}

/* footer */
.footer-line{left:0;top:2936px;width:1200px;height:4px;background:var(--red)}
.foot-col{top:2996px}
.foot-col h5{font-family:"Arvo",Georgia,serif;font-size:15px;font-weight:700;color:#222;margin-bottom:20px;letter-spacing:.5px}
.foot-col li{list-style:none;font-size:12px;color:#666;line-height:26px}
.subscribe{display:flex;height:36px;margin-top:12px}
.subscribe .in{flex:1;border:1px solid #ccc;font-size:12px;color:#999;display:flex;align-items:center;padding-left:12px}
.subscribe .go{width:94px;background:var(--red);color:#fff;font-size:12px;font-weight:700;display:flex;align-items:center;justify-content:center}
.socials{display:flex;gap:8px;margin-top:12px}
.socials span{width:32px;height:32px;border-radius:50%}
.bottom-rule{left:99px;top:3225px;width:1002px;height:1px;background:var(--line)}
.copy{left:0;top:3244px;width:1200px;text-align:center;font-size:12px;color:#666}
</style>
</head>
<body>

<!-- header -->
<div class="abs brand"><span class="dot"></span>Bim-Zee</div>
<div class="abs topbar">
  <span class="phone">
    <svg width="22" height="22" viewBox="0 0 22 22"><circle cx="11" cy="11" r="10" fill="none" stroke="#e8262d" stroke-width="1.5"/><path d="M7.5 6.5l2 0 1 2.5-1.3 1c.6 1.3 1.5 2.2 2.8 2.8l1-1.3 2.5 1v2c-4 .3-8.3-4-8-8z" fill="#e8262d"/></svg>
    1 555 010 0199
  </span>
  <span class="login">&#9679; LOGIN</span>
</div>
<nav class="abs nav">
  <span class="on">Home</span><span>About Us</span><span>News</span><span>Fun Stories</span><span>Gallery</span><span>Contact Us</span>
  <svg width="18" height="18" viewBox="0 0 18 18"><circle cx="7.5" cy="7.5" r="5.5" fill="none" stroke="#222" stroke-width="2.2"/><path d="M11.5 11.5l5 5" stroke="#222" stroke-width="2.4"/></svg>
</nav>

<!-- hero -->
<section class="abs hero">
  <div class="abs hero-pizza" role="img" aria-label="Overhead photo of a tomato and basil pizza"></div>
  <div class="abs hero-title">Bim-Zee</div>
  <div class="abs hero-rule"></div>
  <p class="abs hero-text">At vero eos et accusamus et iusto odio dignissimos ducm us qui blanditiis praesentium voluptatum.</p>
  <div class="abs hero-btn">GET MORE INFO &gt;&gt;</div>
  <div class="abs slide-arrow" style="left:0"><svg width="12" height="20"><path d="M10 2L2 10l8 8" fill="none" stroke="#fff" stroke-width="2"/></svg></div>
  <div class="abs slide-arrow" style="right:0"><svg width="12" height="20"><path d="M2 2l8 8-8 8" fill="none" stroke="#fff" stroke-width="2"/></svg></div>
</section>

<!-- top news -->
<h2 class="abs section-title" style="left:0;width:1200px;text-align:center;top:586px">Top News</h2>

<article class="abs news-card" style="left:99px">
  <div class="photo" role="img" aria-label="Sliced pizza with basil on a wooden board" style="background:linear-gradient(135deg,#c9a27a,#8a5a34)"><span class="tag">TRADING</span></div>
  <h3>At vero eos et accusamus et iusto odio dignissimos ducimus blanditiis</h3>
  <div class="meta"><span class="r">&#9632;</span> May 26, 2016 | <span class="r">&#9650;</span> Like(0) | <span class="r">&#9660;</span> Dislike(0)</div>
</article>
<article class="abs news-card" style="left:439px">
  <div class="photo" role="img" aria-label="Loaded pizza with peppers and olives" style="background:linear-gradient(135deg,#d9a35a,#9c3b22)"><span class="tag">TENDER</span></div>
  <h3>At vero eos et accusamus et iusto odio dignissimos ducimus blanditiis</h3>
  <div class="meta"><span class="r">&#9632;</span> May 26, 2016 | <span class="r">&#9650;</span> Like(0) | <span class="r">&#9660;</span> Dislike(0)</div>
</article>
<article class="abs news-card" style="left:783px">
  <div class="photo" role="img" aria-label="Group of friends laughing and sharing pizza" style="background:linear-gradient(135deg,#b88f7a,#5a4a52)"><span class="tag">INSIGHT</span></div>
  <h3>At vero eos et accusamus et iusto odio dignissimos ducimus blanditiis</h3>
  <div class="meta"><span class="r">&#9632;</span> May 26, 2016 | <span class="r">&#9650;</span> Like(0) | <span class="r">&#9660;</span> Dislike(0)</div>
</article>

<div class="abs divider"></div>
<div class="abs pager-pair">
  <span class="circle-btn"><svg width="12" height="18"><path d="M9 2L3 9l6 7" fill="none" stroke="#666" stroke-width="2"/></svg></span>
  <span class="circle-btn"><svg width="12" height="18"><path d="M3 2l6 7-6 7" fill="none" stroke="#666" stroke-width="2"/></svg></span>
</div>

<!-- fun stories -->
<h2 class="abs section-title" style="left:99px;top:1068px">Fun Stories</h2>

<article class="abs story" style="top:1115px">
  <div class="photo" role="img" aria-label="Friends sharing pizza at a restaurant table" style="background:linear-gradient(135deg,#c99a78,#6b4a3a)"></div>
  <h3>Neque porro quisquam est qui dolorem ipsum quia dolo</h3>
  <div class="meta"><span class="r">&#9632;</span> Feb 06, 2016 &nbsp;| <span class="r">&#9679;</span> Mara Quill</div>
  <p>Lorem Ipsum is simply dummy text of the printing and typesetting industry. Lorem Ipsum has been the industry's standard dummy text ever since the 1500s, when an unknown printer took a galley of type and scrambled it to make a type specimen book.</p>
  <span class="more">READ MORE &gt;&gt;</span>
  <div class="share-bar"><span class="pill">Like</span><span class="count">200</span><span class="pill">Post</span><span class="count">200</span><span class="pill">+1</span><span class="count">200</span><span class="end">&#8599; (3)</span></div>
</article>

<article class="abs story" style="top:1731px">
  <div class="photo" role="img" aria-label="Hands reaching for slices of a pizza on a dark table" style="background:linear-gradient(135deg,#3d4a4f,#a0764a)"></div>
  <h3>Neque porro quisquam est qui dolorem ipsum quia dolo</h3>
  <div class="meta"><span class="r">&#9632;</span> Feb 06, 2016 &nbsp;| <span class="r">&#9679;</span> Mara Quill</div>
  <p>Lorem Ipsum is simply dummy text of the printing and typesetting industry. Lorem Ipsum has been the industry's standard dummy text ever since the 1500s, when an unknown printer took a galley of type and scrambled it to make a type specimen book.</p>
  <span class="more">READ MORE &gt;&gt;</span>
  <div class="share-bar"><span class="pill">Like</span><span class="count">200</span><span class="pill">Post</span><span class="count">200</span><span class="pill">+1</span><span class="count">200</span><span class="end">&#8599; (3)</span></div>
</article>

<div class="abs pagination"><span>Prev</span><span class="on">1</span><span>2</span><span>3</span><span>4</span><span>5</span><span>6</span><span>...</span><span>22</span><span>Next</span></div>

<!-- sidebar -->
<h2 class="abs section-title side" style="top:1068px;font-size:22px">Periodic Communication</h2>
<div class="abs side box" style="top:1115px;height:197px;padding:20px 16px">
  <div class="email-input">ENTER YOUR EMAIL ADDRESS</div>
  <div class="red-btn" style="height:44px;margin-top:14px;font-size:14px">SIGN UP</div>
  <p class="small" style="margin-top:14px">By signing up, you are opting in to receive periodic communications from Bim-Zee</p>
</div>
<div class="abs side side-rule" style="top:1346px"></div>

<h2 class="abs section-title side" style="top:1373px;font-size:22px">Join Us on Pagebook</h2>
<div class="abs side box" style="top:1422px;height:268px;padding:6px">
  <div role="img" aria-label="Page cover photo of a pizza" style="height:150px;background:linear-gradient(135deg,#5a4030,#c0532e);position:relative">
    <div style="position:absolute;left:8px;top:14px;width:80px;height:80px;background:#fff;display:flex;align-items:center;justify-content:center;font-family:Arvo,serif;font-weight:700;font-size:15px;color:#333">Bim-Zee</div>
    <div style="position:absolute;left:100px;top:14px;color:#fff;font-weight:700;font-size:15px">BIM-ZEE<br><span style="font-size:11px;font-weight:400">4,893 LIKES</span></div>
    <div style="position:absolute;left:8px;bottom:12px;background:#f2f2f2;font-size:12px;font-weight:700;padding:4px 10px;color:#333">Like Page</div>
    <div style="position:absolute;right:10px;bottom:12px;background:#f2f2f2;font-size:12px;font-weight:700;padding:4px 10px;color:#333">Sign Up</div>
  </div>
  <p class="small" style="margin:12px 6px 8px;font-size:11px">Be the first of your friends to like this</p>
  <div style="display:flex;gap:4px;padding:0 6px">
    <span role="img" aria-label="Member photo" style="width:50px;height:48px;background:#9a8878"></span>
    <span role="img" aria-label="Member photo" style="width:50px;height:48px;background:#7c8a96"></span>
    <span role="img" aria-label="Member photo" style="width:50px;height:48px;background:#a08a7a"></span>
    <span role="img" aria-label="Member photo" style="width:50px;height:48px;background:#6e7a70"></span>
    <span role="img" aria-label="Member photo" style="width:50px;height:48px;background:#b09888"></span>
    <span role="img" aria-label="Member photo" style="width:50px;height:48px;background:#8c7c8e"></span>
  </div>
</div>
<div class="abs side side-rule" style="top:1726px"></div>

<h2 class="abs section-title side" style="top:1748px;font-size:22px">Our Blog</h2>
<div class="abs side" style="top:1810px;display:flex;flex-direction:column;gap:20px">
  <div class="blog-item"><div class="photo" role="img" aria-label="Pizza on a table" style="background:linear-gradient(135deg,#c48d5e,#7a3a22)"></div><div><h4>At vero eos et accusamus et iusto odio dignissimos ducim</h4><div class="meta" style="margin-top:8px"><span class="r">&#9632;</span> Feb 06, 2016</div></div></div>
  <div class="blog-item"><div class="photo" role="img" aria-label="Friends at a dinner table" style="background:linear-gradient(135deg,#a98a70,#5e4a40)"></div><div><h4>At vero eos et accusamus et iusto odio dignissimos ducim</h4><div class="meta" style="margin-top:8px"><span class="r">&#9632;</span> Feb 06, 2016</div></div></div>
  <div class="blog-item"><div class="photo" role="img" aria-label="Group enjoying pizza" style="background:linear-gradient(135deg,#c7a58c,#7e6050)"></div><div><h4>At vero eos et accusamus et iusto odio dignissimos ducim</h4><div class="meta" style="margin-top:8px"><span class="r">&#9632;</span> Feb 06, 2016</div></div></div>
</div>
<div class="abs side" style="top:2122px;font-size:13px;font-weight:700;color:var(--red)">VIEW MORE &gt;&gt;</div>
<div class="abs side side-rule" style="top:2170px"></div>

<div class="abs side box" style="top:2194px;height:176px;padding:18px 16px">
  <h2 class="section-title" style="font-size:22px">Comment</h2>
  <div style="border:1px solid #ccc;height:44px;margin-top:18px;position:relative"><svg style="position:absolute;right:10px;top:12px" width="18" height="18" viewBox="0 0 18 18"><path d="M3 15l1-4 8-8 3 3-8 8z" fill="none" stroke="#999" stroke-width="1.5"/></svg></div>
  <div class="red-btn" style="width:94px;height:34px;margin-top:14px;font-size:12px">COMMENT</div>
</div>

<div class="abs rule" style="top:2418px"></div>

<!-- gallery -->
<h2 class="abs section-title" style="left:0;width:1200px;text-align:center;top:2463px">Our Gallery</h2>
<div class="abs gallery">
  <div class="photo" role="img" aria-label="Friends in sunglasses laughing together" style="background:linear-gradient(135deg,#d8a070,#8c4a3a)"></div>
  <div class="photo" role="img" aria-label="Pizza slices shared over a table" style="background:linear-gradient(135deg,#3c4548,#9a7248)"></div>
  <div class="photo" role="img" aria-label="Pizza being topped with flour on a dark background" style="background:linear-gradient(135deg,#1e1e1e,#a86a3a)"></div>
  <div class="photo" role="img" aria-label="Group dining outdoors" style="background:linear-gradient(135deg,#c7b2a0,#6e5a4a)"></div>
</div>
<span class="abs circle-btn" style="left:48px;top:2594px"><svg width="12" height="18"><path d="M9 2L3 9l6 7" fill="none" stroke="#666" stroke-width="2"/></svg></span>
<span class="abs circle-btn" style="left:1106px;top:2594px"><svg width="12" height="18"><path d="M3 2l6 7-6 7" fill="none" stroke="#666" stroke-width="2"/></svg></span>

<div class="abs rule" style="top:2764px"></div>

<!-- partners -->
<div class="abs partner" style="left:200px;width:210px;background:#ececec;border-radius:6px" role="img" aria-label="Partner badge"></div>
<div class="abs partner" style="left:494px;width:212px;background:#f3d3d4;border-radius:6px" role="img" aria-label="Partner badge"></div>
<div class="abs partner" style="left:790px;width:210px;background:#ececec;border-radius:6px" role="img" aria-label="Partner badge"></div>

<!-- footer -->
<div class="abs footer-line"></div>
<div class="abs foot-col" style="left:99px"><h5>RESOURCES</h5><ul><li>Learn</li><li>Community</li><li>Documentation</li><li>FAQ</li><li>Services Status</li><li>Certification</li></ul></div>
<div class="abs foot-col" style="left:295px"><h5>HELP &amp; SUPPORT</h5><ul><li>Recommended Reading</li><li>Submit your Story</li><li>Contact Us</li><li>Frequently Asked Questions</li><li>How to Order</li></ul></div>
<div class="abs foot-col" style="left:553px"><h5>QUICK LINKS</h5><ul><li>Blog</li><li>Events</li><li>Careers</li><li>Press</li><li>Contact</li><li>Partners</li></ul></div>
<div class="abs foot-col" style="left:778px;width:323px">
  <h5 style="margin-bottom:10px">EMAIL SUBSCRIPTION</h5>
  <p style="font-size:12px;color:#666">Register your email address to get information about us</p>
  <div class="subscribe"><span class="in">Email Address</span><span class="go">SUBSCRIBE</span></div>
  <h5 style="margin:18px 0 0">STAY CONNECTED</h5>
  <div class="socials"><span style="background:#4caf7a"></span><span style="background:#3b5998"></span><span style="background:#35a7e0"></span><span style="background:#d84a38"></span><span style="background:#517fa4"></span><span style="background:#2fa6d6"></span><span style="background:#cc1f1f"></span><span style="background:#c8232c"></span></div>
</div>
<div class="abs bottom-rule"></div>
<div class="abs copy">Copyrights © 2017, Bim-Zee. All Rights Reserved &nbsp;| &nbsp;Privacy Policy | Terms of Use | Feedback</div>

</body>
</html>
```